Business Card Design

We need a business card design for a Dry cleaners in Brisbane, Australia. We are trying to promote a fresh/clean image consistent with our website. www.pinnelgarmentcare.com.au

Looking for a professional neat card that's easy to read.

Target Market(s)

Customers looking for a professional, fresh and clean drycleaners.

Industry/Entity Type

Business

Contact Information for Business Card

See our existing business card. The Fax number (07) 3468 5270 to be removed.

Requirements
Must have
• All the details on current business card less the fax number.
Nice to have
• I like white text on coloured background. Blue works well as we are located near the water...

```html
<!DOCTYPE html>
<html lang="en">
<head>
<meta charset="utf-8">
<title>Pinnel Garment Care – Business Card</title>
<link rel="stylesheet" href="https://fonts.googleapis.com/css2?family=Arimo:ital,wght@0,400;0,700;1,400;1,700&display=swap">
<style>
  :root {
    --navy: #34449a;
    --red: #e8333b;
    --card: #f7f7f8;
    --backdrop: #e9eaec;
    --ink: #34449a;
  }
  * { box-sizing: border-box; margin: 0; padding: 0; }
  html, body {
    width: 1200px;
    height: 900px;
    overflow: hidden;
    background: var(--backdrop);
    font-family: "Arimo", Arial, sans-serif;
  }
  .canvas {
    position: relative;
    width: 1200px;
    height: 900px;
  }
  .card {
    position: absolute;
    left: 260px;
    width: 680px;
    height: 388px;
    border-radius: 26px;
    background: linear-gradient(135deg, #ffffff 0%, var(--card) 55%, #ececee 100%);
    box-shadow: 0 10px 28px rgba(0, 0, 0, 0.16);
    overflow: hidden;
  }
  .card--front { top: 42px; }
  .card--back { top: 470px; }

  .wordmark {
    display: flex;
    align-items: center;
    gap: 14px;
    color: var(--navy);
    font-weight: 700;
    font-style: normal;
    white-space: nowrap;
  }
  .wordmark__dot {
    display: block;
    border-radius: 50%;
    background: var(--red);
    flex: none;
  }
  .card--front .wordmark {
    position: absolute;
    left: 0; right: 0; top: 0; bottom: 0;
    justify-content: center;
    font-size: 46px;
  }
  .card--front .wordmark__dot { width: 30px; height: 30px; }

  .side-band {
    position: absolute;
    left: 0; top: 0;
    width: 160px;
    height: 388px;
  }

  .contact-block {
    position: absolute;
    left: 178px;
    top: 70px;
    color: var(--ink);
  }
  .person__name {
    font-size: 30px;
    font-weight: 700;
    font-style: italic;
  }
  .person__role {
    margin-top: 6px;
    margin-left: -12px;
    font-size: 22px;
    font-style: italic;
    font-weight: 400;
  }
  .details {
    list-style: none;
    margin-top: 48px;
    margin-left: -24px;
  }
  .details li {
    display: flex;
    align-items: center;
    gap: 10px;
    font-size: 19px;
    font-style: italic;
    line-height: 27px;
  }
  .details svg { width: 17px; height: 17px; flex: none; }

  .card--back .wordmark {
    position: absolute;
    right: 36px;
    top: 138px;
    gap: 10px;
    font-size: 28px;
  }
  .card--back .wordmark__dot { width: 18px; height: 18px; }
</style>
</head>
<body>
<main class="canvas">

  <section class="card card--front" aria-label="Card front">
    <div class="wordmark">
      <span class="wordmark__dot"></span>
      <span class="wordmark__name">Pinnel Garment Care</span>
    </div>
  </section>

  <section class="card card--back" aria-label="Card back">
    <svg class="side-band" viewBox="0 0 160 388" aria-hidden="true">
      <path d="M0 0 H150 C96 60 92 180 96 388 H0 Z" fill="var(--red)"/>
      <path d="M0 0 H118 C68 60 66 180 72 388 H0 Z" fill="var(--navy)"/>
    </svg>

    <div class="contact-block">
      <h1 class="person__name">Owen Harlow</h1>
      <p class="person__role">Founder</p>
      <ul class="details">
        <li>
          <svg viewBox="0 0 16 16"><rect x="4" y="1" width="8" height="14" rx="1.5" fill="none" stroke="var(--navy)" stroke-width="1.6"/><circle cx="8" cy="12.4" r="0.9" fill="var(--navy)"/></svg>
          <span>012 345 6789</span>
        </li>
        <li>
          <svg viewBox="0 0 16 16"><rect x="1" y="3.5" width="14" height="9" fill="var(--navy)"/><path d="M1 3.5 L8 9 L15 3.5" fill="none" stroke="#fff" stroke-width="1.2"/></svg>
          <span>urname@email.com</span>
        </li>
        <li>
          <svg viewBox="0 0 16 16"><g fill="none" stroke="var(--navy)" stroke-width="1.3"><circle cx="8" cy="8" r="6.5"/><ellipse cx="8" cy="8" rx="3" ry="6.5"/><path d="M1.5 8 H14.5 M2.6 4.5 H13.4 M2.6 11.5 H13.4"/></g></svg>
          <span>www.pinnelgarmentcare.com.au</span>
        </li>
        <li>
          <svg viewBox="0 0 16 16"><circle cx="8" cy="8" r="7" fill="var(--navy)"/></svg>
          <span>@pinnelcare</span>
        </li>
      </ul>
    </div>

    <div class="wordmark">
      <span class="wordmark__dot"></span>
      <span class="wordmark__name">Pinnel Garment Care</span>
    </div>
  </section>

</main>
</body>
</html>
```